High-end construction company needs a business card design

We need a modern looking business card that draws people in, is memorable and looks so good people will want to sick it on their fridges.
On the first side what is needed are:
Logo
My name - Tomasz Brelwik
Title - Managing Director
Website - www.varkelt.co.uk
Email - tomasz@varkelt.co.uk
Telephone - 020 5194 6281
Mobile - 07845139072
On the back side was is needed is a list of all the services we provide:
-Kitchen Renovations
-Bathroom Renovations
-House Renovations
-Garage Conversions
-Extensions
-Loft Conversions
-Conservatories
-Carpentry
-Tiling
-Electrical
-Plumbing & Heating
-Bricklaying
-Landscaping
-Decorating
-Plastering
We would like the colours to be the same shades as on the logo with grey or black for the words.
Target Market(s)
Anyone who needs building work done
Contact Information for Business Card
This business card is for a construction company which strives to deliver excellent service and quality.
The look and feel of the card should represent this.
Requirements
Must have
- On the first side what is needed are:
Logo
My name - Tomasz Brelwik
Title - Managing Director
Website - www.varkelt.co.uk
Email - tomasz@varkelt.co.uk
Telephone - 020 5194 6281
Mobile - 07845139072
Nice to have
- Cool looking features

```html
<!DOCTYPE html>
<html lang="en">
<head>
<meta charset="utf-8">
<title>Varkelt Construction Ltd – Business Card</title>
<link href="https://fonts.googleapis.com/css2?family=Arimo:wght@400;700&display=swap" rel="stylesheet">
<style>
  :root {
    --stage: #1c1c1c;
    --green: #74bd43;
    --green-dark: #3f8f3a;
    --paper: #ffffff;
    --ink-light: #ffffff;
  }
  * { box-sizing: border-box; margin: 0; padding: 0; }
  html, body { width: 1200px; height: 1015px; overflow: hidden; }
  body {
    background: var(--stage);
    font-family: "Arimo", Arial, sans-serif;
    position: relative;
  }
  .card {
    position: absolute;
    width: 620px;
    height: 354px;
    background: var(--paper);
    overflow: hidden;
    box-shadow: 0 18px 40px rgba(0,0,0,.6);
  }
  .card--back { left: 60px; top: 70px; }
  .card--front { left: 520px; top: 590px; }
  .card__wave { position: absolute; inset: 0; width: 100%; height: 100%; }

  .services {
    position: absolute;
    top: 30px;
    left: 32px;
    display: flex;
    gap: 40px;
    color: var(--ink-light);
    font-size: 16px;
    line-height: 21px;
  }
  .services ul { list-style: none; }
  .services li { position: relative; padding-left: 17px; }
  .services li::before {
    content: "";
    position: absolute;
    left: 0; top: 6px;
    width: 9px; height: 9px;
    border-radius: 50%;
    background: var(--ink-light);
  }

  .brand {
    position: absolute;
    display: flex;
    align-items: center;
    gap: 12px;
    color: var(--green);
    font-weight: 700;
    text-transform: uppercase;
    line-height: 1.05;
  }
  .brand__mark {
    width: 20px; height: 20px;
    background: var(--green);
    flex: none;
  }
  .brand__name { font-size: 30px; letter-spacing: 1px; }
  .brand__name small { display: block; font-size: 13px; letter-spacing: 2px; }
  .card--back .brand { right: 30px; top: 222px; }
  .card--front .brand { left: 54px; top: 118px; }
  .card--front .brand__name { font-size: 38px; }
  .card--front .brand__name small { font-size: 16px; }

  .contact {
    position: absolute;
    right: 26px;
    bottom: 24px;
    text-align: right;
    color: var(--ink-light);
  }
  .contact__name { font-size: 20px; line-height: 24px; font-weight: 700; text-transform: uppercase; letter-spacing: .5px; }
  .contact__title { font-size: 15px; line-height: 19px; margin-bottom: 10px; }
  .contact__line {
    display: flex; justify-content: flex-end; align-items: center; gap: 8px;
    font-size: 15px; line-height: 21px;
  }
  .contact__line svg { width: 13px; height: 13px; flex: none; }
</style>
</head>
<body>

<section class="card card--back" aria-label="Card back: services">
  <svg class="card__wave" viewBox="0 0 620 354" aria-hidden="true">
    <path d="M0,0 H620 V80 C520,80 470,110 430,170 C380,250 300,330 120,354 H0 Z" fill="var(--green)"/>
    <path d="M630,94 C528,94 482,124 442,184 C394,262 318,342 140,364" fill="none" stroke="var(--green-dark)" stroke-width="5"/>
    <path d="M630,106 C534,106 490,136 452,196 C404,272 330,350 160,372" fill="none" stroke="var(--green)" stroke-width="1.5"/>
  </svg>
  <div class="services">
    <ul>
      <li>Kitchen Renovations</li>
      <li>Bathroom Renovations</li>
      <li>House Renovations</li>
      <li>Garage Conversions</li>
      <li>Extensions</li>
      <li>Loft Conversions</li>
      <li>Conservatories</li>
      <li>Carpentry</li>
    </ul>
    <ul>
      <li>Tiling</li>
      <li>Electrical</li>
      <li>Plumbing &amp; Heating</li>
      <li>Bricklaying</li>
      <li>Landscaping</li>
      <li>Decorating</li>
      <li>Plastering</li>
    </ul>
  </div>
  <div class="brand">
    <span class="brand__mark"></span>
    <span class="brand__name">Varkelt<small>Construction Ltd</small></span>
  </div>
</section>

<section class="card card--front" aria-label="Card front: contact">
  <svg class="card__wave" viewBox="0 0 620 354" aria-hidden="true">
    <path d="M620,95 C500,100 450,130 405,190 C360,250 300,330 160,354 H620 Z" fill="var(--green)"/>
    <path d="M630,80 C490,86 438,116 392,176 C346,238 286,316 110,342" fill="none" stroke="var(--green-dark)" stroke-width="5"/>
    <path d="M630,68 C482,74 428,104 382,164 C336,226 276,302 90,330" fill="none" stroke="var(--green)" stroke-width="1.5"/>
  </svg>
  <div class="brand">
    <span class="brand__mark"></span>
    <span class="brand__name">Varkelt<small>Construction Ltd</small></span>
  </div>
  <div class="contact">
    <p class="contact__name">Tomasz Brelwik</p>
    <p class="contact__title">Managing Director</p>
    <p class="contact__line">020 5194 6281
      <svg viewBox="0 0 14 14" aria-hidden="true"><path d="M3,1 L5,1 L6,4 L4.5,5.5 C5.5,7.5 6.5,8.5 8.5,9.5 L10,8 L13,9 L13,11 C13,12 12,13 11,13 C6,13 1,8 1,3 C1,2 2,1 3,1 Z" fill="#fff"/></svg>
    </p>
    <p class="contact__line">07845139072
      <svg viewBox="0 0 14 14" aria-hidden="true"><rect x="3.5" y="1" width="7" height="12" rx="1.2" fill="none" stroke="#fff" stroke-width="1.5"/><circle cx="7" cy="11" r=".8" fill="#fff"/></svg>
    </p>
    <p class="contact__line">tomasz@varkelt.co.uk
      <svg viewBox="0 0 14 14" aria-hidden="true"><rect x="1" y="3" width="12" height="8" fill="#fff"/><path d="M1,3 L7,8 L13,3" fill="none" stroke="var(--green)" stroke-width="1"/></svg>
    </p>
    <p class="contact__line">www.varkelt.co.uk
      <svg viewBox="0 0 14 14" aria-hidden="true"><circle cx="7" cy="7" r="6" fill="none" stroke="#fff" stroke-width="1.3"/><ellipse cx="7" cy="7" rx="2.5" ry="6" fill="none" stroke="#fff" stroke-width="1"/><path d="M1,7 H13" stroke="#fff" stroke-width="1"/></svg>
    </p>
  </div>
</section>

</body>
</html>
```